Harborline Outpost Registry needs a web design

We are launching a new website and need a web design. The website is going to list every military base and installment around the world with information on each base such as a description of the base, the history of the base, contact information at the base, address, lat/long of the base, and any other relevant information including images of the base. We need a home page with navigation menu and the design of the military base page so that every military base page is formatted the same for the referenced information. We have included an example of the content that may be found on the base page(s). We are also going to have the information available in spanish.

We also wanted to mention we will be building this website in wordpress.

We also wanted to note that in the format of each base page, we will have a frequently asked questions section with answers.

```html
<!DOCTYPE html>
<html lang="en">
<head>
<meta charset="utf-8">
<title>Harborline Outpost Registry</title>
<link rel="stylesheet" href="https://fonts.googleapis.com/css2?family=Titillium+Web:wght@600;700&family=Open+Sans:wght@400;600&display=swap">
<style>
:root{
  --accent:#ff5a1f;
  --ink:#1c1c1c;
  --heading:#2a2a2a;
  --muted:#555;
  --white:#fff;
  --footer:#262626;
  --card-border:#e6e6e6;
}
*{box-sizing:border-box;margin:0;padding:0}
html,body{width:1200px;height:2961px;overflow:hidden;background:var(--white);font-family:"Open Sans",Arial,sans-serif;color:var(--ink)}
.page{position:relative;width:1200px;height:2961px}
.hero{position:absolute;left:0;top:0;width:1200px;height:514px;
  background:radial-gradient(circle at 29% 26%,#ffd96a 0,#f3a723 9%,#c9791a 24%,#7a3f0c 55%,#3a1d06 100%)}
.hero-shade{position:absolute;inset:0;background:linear-gradient(180deg,rgba(40,18,2,.25),rgba(40,18,2,0) 40%,rgba(40,18,2,.45))}
.brand{position:absolute;left:113px;top:22px;font-family:"Titillium Web",sans-serif;font-weight:700;font-size:29px;color:var(--white);letter-spacing:.3px}
.nav{position:absolute;top:28px;left:508px;display:flex;gap:36px}
.nav a{color:var(--white);text-decoration:none;font-size:16px}
.btn{display:inline-flex;align-items:center;justify-content:center;background:var(--accent);color:var(--white);font-size:16px;font-weight:600;text-decoration:none}
.quote{position:absolute;left:961px;top:18px;width:129px;height:44px}
.hero-title{position:absolute;top:248px;width:1200px;text-align:center;font-family:"Titillium Web",sans-serif;font-weight:700;font-size:42px;color:var(--white)}
.search{position:absolute;left:330px;top:333px;width:540px;height:44px;display:flex}
.search-field{flex:1;background:var(--white);display:flex;align-items:center;padding-left:20px;gap:12px;font-size:15px;color:#555}
.search-btn{width:109px;height:44px}
.section-title{position:absolute;left:110px;top:582px;font-family:"Titillium Web",sans-serif;font-weight:700;font-size:42px;color:var(--ink)}
.list{position:absolute;left:110px;top:683px;width:978px;display:flex;flex-direction:column;gap:42px}
.card{position:relative;height:275px;display:flex;border:1px solid var(--card-border);box-shadow:0 3px 8px rgba(0,0,0,.08);background:var(--white)}
.card-photo{width:275px;height:100%;flex:none}
.card-body{padding:30px 0 0 42px}
.card-title{font-family:"Titillium Web",sans-serif;font-weight:600;font-size:26px;color:var(--heading);line-height:1.2}
.card-sub{font-size:18px;color:var(--muted);margin-top:7px}
.detail{display:flex;align-items:center;gap:14px;font-size:18px;color:var(--ink);margin-top:17px}
.detail svg{flex:none}
.coords{font-size:18px;color:#444;margin:11px 0 0 34px}
.learn{position:absolute;left:813px;top:39px;width:133px;height:44px}
.load{position:absolute;left:534px;top:2620px;width:204px;height:44px;font-weight:400}
.footer{position:absolute;left:0;top:2731px;width:1200px;height:230px;background:var(--footer);color:var(--white);text-align:center}
.footer-brand{position:absolute;top:52px;width:100%;font-family:"Titillium Web",sans-serif;font-weight:700;font-size:29px}
.footer-nav{position:absolute;top:107px;width:100%;display:flex;justify-content:center;gap:36px}
.footer-nav a{color:var(--white);text-decoration:none;font-size:16px}
.copy{position:absolute;top:150px;width:100%;font-size:16px}
</style>
</head>
<body>
<div class="page">
  <header class="hero">
    <div role="img" aria-label="Soldiers walking across the desert at sunset beneath a helicopter" style="position:absolute;inset:0"></div>
    <div class="hero-shade"></div>
    <div class="brand">HARBORLINE</div>
    <nav class="nav"><a href="#">Home</a><a href="#">About</a><a href="#">Military Base</a><a href="#">Blog</a><a href="#">Contact</a></nav>
    <a class="btn quote" href="#">Get Quote</a>
    <h1 class="hero-title">HARBORLINE OUTPOST REGISTRY</h1>
    <form class="search">
      <div class="search-field">
        <svg width="18" height="18" viewBox="0 0 18 18" fill="none" stroke="#888" stroke-width="1.6"><circle cx="7.5" cy="7.5" r="6"/><path d="M12 12l5 5"/></svg>
        Search Military Base
      </div>
      <span class="btn search-btn">Search</span>
    </form>
  </header>

  <h2 class="section-title">MILITARY BASE</h2>

  <main class="list">
    <article class="card">
      <div class="card-photo" role="img" aria-label="Soldiers and helicopter silhouetted at sunset" style="background:linear-gradient(180deg,#8a8fa6 0%,#e6a160 55%,#3b2a22 100%)"></div>
      <div class="card-body">
        <h3 class="card-title">FORT CALLOWAY OUTPOST</h3>
        <p class="card-sub">History, Facilities, and Support Services</p>
        <p class="detail"><svg width="20" height="20" viewBox="0 0 24 24"><path fill="var(--accent)" d="M6.6 10.8a15 15 0 006.6 6.6l2.2-2.2a1 1 0 011-.25 11.4 11.4 0 003.6.57 1 1 0 011 1V20a1 1 0 01-1 1A17 17 0 013 4a1 1 0 011-1h3.5a1 1 0 011 1 11.4 11.4 0 00.57 3.6 1 1 0 01-.25 1z"/></svg>(555) 014-2290</p>
        <p class="detail"><svg width="20" height="22" viewBox="0 0 24 24"><path fill="var(--accent)" d="M12 2a7 7 0 00-7 7c0 5 7 13 7 13s7-8 7-13a7 7 0 00-7-7zm0 9.5A2.5 2.5 0 1112 6.5a2.5 2.5 0 010 5z"/></svg>Calloway Ridge, KY, United States</p>
        <p class="coords">Latitude: 36.4120° N Longitude: 84.2035° W DSN</p>
      </div>
      <a class="btn learn" href="#">Learn More</a>
    </article>
    <article class="card">
      <div class="card-photo" role="img" aria-label="Armed soldiers in camouflage gear in a forest clearing" style="background:linear-gradient(160deg,#6f7d54 0%,#8b8560 50%,#4e4a36 100%)"></div>
      <div class="card-body">
        <h3 class="card-title">LOREM IPSUM DOLOR SIT AMET</h3>
        <p class="card-sub">History, Facilities, and Support Services</p>
        <p class="detail"><svg width="20" height="20" viewBox="0 0 24 24"><path fill="var(--accent)" d="M6.6 10.8a15 15 0 006.6 6.6l2.2-2.2a1 1 0 011-.25 11.4 11.4 0 003.6.57 1 1 0 011 1V20a1 1 0 01-1 1A17 17 0 013 4a1 1 0 011-1h3.5a1 1 0 011 1 11.4 11.4 0 00.57 3.6 1 1 0 01-.25 1z"/></svg>+1888-888-8888</p>
        <p class="detail"><svg width="20" height="22" viewBox="0 0 24 24"><path fill="var(--accent)" d="M12 2a7 7 0 00-7 7c0 5 7 13 7 13s7-8 7-13a7 7 0 00-7-7zm0 9.5A2.5 2.5 0 1112 6.5a2.5 2.5 0 010 5z"/></svg>Lorem ipsum dolor sit amet</p>
        <p class="coords">Latitude: 36.4120° N Longitude: 84.2035° W DSN</p>
      </div>
      <a class="btn learn" href="#">Learn More</a>
    </article>
    <article class="card">
      <div class="card-photo" role="img" aria-label="Soldiers walking on a dusty desert track" style="background:linear-gradient(180deg,#e9dccb 0%,#c9ab84 55%,#8d7256 100%)"></div>
      <div class="card-body">
        <h3 class="card-title">LOREM IPSUM DOLOR SIT AMET</h3>
        <p class="card-sub">History, Facilities, and Support Services</p>
        <p class="detail"><svg width="20" height="20" viewBox="0 0 24 24"><path fill="var(--accent)" d="M6.6 10.8a15 15 0 006.6 6.6l2.2-2.2a1 1 0 011-.25 11.4 11.4 0 003.6.57 1 1 0 011 1V20a1 1 0 01-1 1A17 17 0 013 4a1 1 0 011-1h3.5a1 1 0 011 1 11.4 11.4 0 00.57 3.6 1 1 0 01-.25 1z"/></svg>+1888-888-8888</p>
        <p class="detail"><svg width="20" height="22" viewBox="0 0 24 24"><path fill="var(--accent)" d="M12 2a7 7 0 00-7 7c0 5 7 13 7 13s7-8 7-13a7 7 0 00-7-7zm0 9.5A2.5 2.5 0 1112 6.5a2.5 2.5 0 010 5z"/></svg>Lorem ipsum dolor sit amet</p>
        <p class="coords">Latitude: 36.4120° N Longitude: 84.2035° W DSN</p>
      </div>
      <a class="btn learn" href="#">Learn More</a>
    </article>
    <article class="card">
      <div class="card-photo" role="img" aria-label="Soldiers with a drone and equipment cases in the desert" style="background:linear-gradient(180deg,#b9cbd6 0%,#cbb99a 50%,#7d7262 100%)"></div>
      <div class="card-body">
        <h3 class="card-title">LOREM IPSUM DOLOR SIT AMET</h3>
        <p class="card-sub">History, Facilities, and Support Services</p>
        <p class="detail"><svg width="20" height="20" viewBox="0 0 24 24"><path fill="var(--accent)" d="M6.6 10.8a15 15 0 006.6 6.6l2.2-2.2a1 1 0 011-.25 11.4 11.4 0 003.6.57 1 1 0 011 1V20a1 1 0 01-1 1A17 17 0 013 4a1 1 0 011-1h3.5a1 1 0 011 1 11.4 11.4 0 00.57 3.6 1 1 0 01-.25 1z"/></svg>+1888-888-8888</p>
        <p class="detail"><svg width="20" height="22" viewBox="0 0 24 24"><path fill="var(--accent)" d="M12 2a7 7 0 00-7 7c0 5 7 13 7 13s7-8 7-13a7 7 0 00-7-7zm0 9.5A2.5 2.5 0 1112 6.5a2.5 2.5 0 010 5z"/></svg>Lorem ipsum dolor sit amet</p>
        <p class="coords">Latitude: 36.4120° N Longitude: 84.2035° W DSN</p>
      </div>
      <a class="btn learn" href="#">Learn More</a>
    </article>
    <article class="card">
      <div class="card-photo" role="img" aria-label="Recruits running through a tire obstacle course" style="background:linear-gradient(180deg,#b8b6ad 0%,#8d8a80 55%,#2c2a27 100%)"></div>
      <div class="card-body">
        <h3 class="card-title">LOREM IPSUM DOLOR SIT AMET</h3>
        <p class="card-sub">History, Facilities, and Support Services</p>
        <p class="detail"><svg width="20" height="20" viewBox="0 0 24 24"><path fill="var(--accent)" d="M6.6 10.8a15 15 0 006.6 6.6l2.2-2.2a1 1 0 011-.25 11.4 11.4 0 003.6.57 1 1 0 011 1V20a1 1 0 01-1 1A17 17 0 013 4a1 1 0 011-1h3.5a1 1 0 011 1 11.4 11.4 0 00.57 3.6 1 1 0 01-.25 1z"/></svg>+1888-888-8888</p>
        <p class="detail"><svg width="20" height="22" viewBox="0 0 24 24"><path fill="var(--accent)" d="M12 2a7 7 0 00-7 7c0 5 7 13 7 13s7-8 7-13a7 7 0 00-7-7zm0 9.5A2.5 2.5 0 1112 6.5a2.5 2.5 0 010 5z"/></svg>Lorem ipsum dolor sit amet</p>
        <p class="coords">Latitude: 36.4120° N Longitude: 84.2035° W DSN</p>
      </div>
      <a class="btn learn" href="#">Learn More</a>
    </article>
    <article class="card">
      <div class="card-photo" role="img" aria-label="Military helicopters parked on an airfield at dusk" style="background:linear-gradient(180deg,#5d8a8c 0%,#6b6a55 50%,#c98a3a 80%,#3a2b1c 100%)"></div>
      <div class="card-body">
        <h3 class="card-title">LOREM IPSUM DOLOR SIT AMET</h3>
        <p class="card-sub">History, Facilities, and Support Services</p>
        <p class="detail"><svg width="20" height="20" viewBox="0 0 24 24"><path fill="var(--accent)" d="M6.6 10.8a15 15 0 006.6 6.6l2.2-2.2a1 1 0 011-.25 11.4 11.4 0 003.6.57 1 1 0 011 1V20a1 1 0 01-1 1A17 17 0 013 4a1 1 0 011-1h3.5a1 1 0 011 1 11.4 11.4 0 00.57 3.6 1 1 0 01-.25 1z"/></svg>+1888-888-8888</p>
        <p class="detail"><svg width="20" height="22" viewBox="0 0 24 24"><path fill="var(--accent)" d="M12 2a7 7 0 00-7 7c0 5 7 13 7 13s7-8 7-13a7 7 0 00-7-7zm0 9.5A2.5 2.5 0 1112 6.5a2.5 2.5 0 010 5z"/></svg>Lorem ipsum dolor sit amet</p>
        <p class="coords">Latitude: 36.4120° N Longitude: 84.2035° W DSN</p>
      </div>
      <a class="btn learn" href="#">Learn More</a>
    </article>
  </main>

  <a class="btn load" href="#">Load More</a>

  <footer class="footer">
    <div class="footer-brand">HARBORLINE</div>
    <nav class="footer-nav"><a href="#">Home</a><a href="#">About</a><a href="#">Military Base</a><a href="#">Blog</a><a href="#">Contact</a></nav>
    <p class="copy">2023 Harborline. All Rights Reserved.</p>
  </footer>
</div>
</body>
</html>
```